New Organic Skin Care Line Needs to Design a Product Label

***THE WINNER OF THIS PROJECT WILL MOST LIKELY BECOME THE EXCLUSIVE DESIGNER FOR OUR OTHER PRODUCT LABELS***

We need a label design for a new organic skin care product line called "Maple Dew Gala." This specific product is a 100% pure organic coconut oil. It's used for skin hydration, protection, and makeup removal.

Info to include on front label:

1. Logo: Maple Dew Gala (attached)
2. Product Name: Pure Coconut Oil (emphasize "organic" somewhere)
3. Slogan: Hydrate your skin and hair.
4. Size: 8 FL OZ 236mL

Attached is:

1. The brand logo "Maple Dew Gala" with a white background.
2. An image of the bottle we will use.
3. An image of the bottle with lines to show the size and placement of the label.
4. The brand logo "Maple Dew Gala" with a black background. (photoshop file)

What we need:

A simple mock up of the front side of the label on the bottle. We first want to know what it will look like on the bottle given the size and dimensions.

- We would like one label with a white background (including the logo with a white background).
- We would like a second label with a black background (including the logo with a black background, just need to make the black font white instead of black).

We can get a great idea of what to expect from the front side of the label so we will complete the back side once we identify a winner.
Updates

Apologies, but we are now using a different bottle. The previous one is now discontinued. Please view the two most recent images uploaded. One is an image of the new bottle by itself. The other is an image of that bottle with instructions. Please use your most recent designs on the new bottle. Feel free to make any modifications you see fit to compliment the new bottle shape. Added Friday, March 18, 2016

Reason: We are still working with the label company to finalize the size. Once the size is confirmed we will have to tweak labels based on finalized measurements.

Target Market(s)

Women, 18-70

Industry/Entity Type

Skin Care Product

Font styles to use
Decorative
Script

Requirements
Must have
• -"shabby sheek" and "cute" theme
• -soft organic feel
• -the ingredients are organic, pure, and natural. That should be an essence of the label.

```html
<!DOCTYPE html>
<html lang="en">
<head>
<meta charset="utf-8">
<title>Maple Dew Gala – Coconut Oil Label Concepts</title>
<link href="https://fonts.googleapis.com/css2?family=Advent+Pro:wght@200&family=Montserrat:wght@300;400;600&display=swap" rel="stylesheet">
<style>
  :root {
    --tan: #e3b572;
    --tan-soft: #efd2a4;
    --ink-black: #000000;
    --paper: #ffffff;
    --brand-pink: #d23a6e;
    --glass: #e6e7e8;
    --glass-edge: #d2d3d5;
    --border: #c9c9c9;
  }
  html, body {
    margin: 0;
    padding: 0;
    width: 1200px;
    height: 1200px;
    overflow: hidden;
    background: var(--paper);
  }
  .board {
    position: relative;
    width: 1200px;
    height: 1200px;
  }
  .flat-label {
    position: absolute;
    width: 522px;
    height: 247px;
    display: block;
  }
  .flat-label--white { left: 78px; top: 44px; outline: 1px solid var(--border); }
  .flat-label--black { left: 619px; top: 44px; }
  .flat-label--tan   { left: 78px; top: 328px; }
  .flat-label--noir  { left: 619px; top: 328px; }

  .bottle {
    position: absolute;
    top: 626px;
    width: 206px;
    height: 500px;
    display: block;
  }
  .bottle--white { left: 106px; }
  .bottle--tan   { left: 378px; }
  .bottle--black { left: 651px; }
  .bottle--noir  { left: 899px; }

  .glass { fill: var(--glass); }
  .glass-seam { fill: var(--glass-edge); }

  .brand-name {
    font-family: "Montserrat", sans-serif;
    font-weight: 400;
    font-size: 10px;
    letter-spacing: 2.4px;
    text-anchor: middle;
  }
  .claim-pct {
    font-family: "Montserrat", sans-serif;
    font-weight: 600;
    font-size: 10.5px;
    text-anchor: middle;
  }
  .claim-organic {
    font-family: "Montserrat", sans-serif;
    font-weight: 300;
    font-size: 14px;
    text-anchor: middle;
  }
  .product-name {
    font-family: "Advent Pro", sans-serif;
    font-weight: 200;
    text-anchor: middle;
  }
  .product-name--coconut { font-size: 48px; }
  .product-name--oil { font-size: 56px; }
  .size-note {
    font-family: "Montserrat", sans-serif;
    font-weight: 400;
    font-size: 6px;
    text-anchor: middle;
  }
</style>
</head>
<body>
<main class="board">

  <svg width="0" height="0" style="position:absolute" aria-hidden="true">
    <defs>
      <linearGradient id="wreath-tone" x1="0" y1="0" x2="1" y2="1">
        <stop offset="0" stop-color="#9acd4a"/>
        <stop offset="0.5" stop-color="#f7c548"/>
        <stop offset="1" stop-color="#8cc63f"/>
      </linearGradient>
      <radialGradient id="noir-glow" cx="0.5" cy="0.72" r="0.6">
        <stop offset="0" stop-color="#4a4a4a"/>
        <stop offset="1" stop-color="#000000"/>
      </radialGradient>
      <radialGradient id="tan-glow" cx="0.5" cy="0.75" r="0.65">
        <stop offset="0" stop-color="#d9a660"/>
        <stop offset="0.5" stop-color="#e3b572"/>
        <stop offset="1" stop-color="#e3b572"/>
      </radialGradient>
      <linearGradient id="white-fade" x1="0" y1="0" x2="1" y2="0">
        <stop offset="0" stop-color="#dcdddf"/>
        <stop offset="0.3" stop-color="#ffffff"/>
        <stop offset="0.7" stop-color="#ffffff"/>
        <stop offset="1" stop-color="#dcdddf"/>
      </linearGradient>

      <path id="wreath-shape" d="M140.7,234 A124,124 0 1 1 381.3,234 L349.5,229 A92,92 0 1 0 172.5,229 Z"/>

      <!-- Shared centre badge, tan disc with white type -->
      <g id="badge-tan">
        <use href="#wreath-shape" fill="url(#wreath-tone)" role="img" aria-label="Wreath of green leaves and golden oil drops"/>
        <circle cx="261" cy="205" r="86" fill="var(--tan)"/>
        <text class="claim-pct" x="261" y="143" fill="var(--paper)">100%</text>
        <text class="claim-organic" x="261" y="158" fill="var(--paper)">PURE ORGANIC</text>
        <text class="product-name product-name--coconut" x="261" y="196" textLength="128" lengthAdjust="spacingAndGlyphs" fill="var(--paper)">COCONUT</text>
        <text class="product-name product-name--oil" x="257" y="240" textLength="56" lengthAdjust="spacingAndGlyphs" fill="var(--paper)">OIL</text>
        <text class="size-note" x="317" y="222" fill="var(--paper)">8 FL OZ</text>
        <text class="size-note" x="317" y="229" fill="var(--paper)">236mL</text>
      </g>

      <!-- White label -->
      <symbol id="label-white" viewBox="0 0 522 320" overflow="visible">
        <rect x="-200" y="0" width="922" height="400" fill="var(--paper)"/>
        <text class="brand-name" x="261" y="64" fill="var(--brand-pink)">MAPLE DEW GALA</text>
        <use href="#badge-tan"/>
      </symbol>

      <!-- Black label, pink name -->
      <symbol id="label-black" viewBox="0 0 522 320" overflow="visible">
        <rect x="-200" y="0" width="922" height="400" fill="var(--ink-black)"/>
        <text class="brand-name" x="261" y="64" fill="var(--brand-pink)">MAPLE DEW GALA</text>
        <use href="#badge-tan"/>
      </symbol>

      <!-- Black label, white name -->
      <symbol id="label-black-white-name" viewBox="0 0 522 320" overflow="visible">
        <rect x="-200" y="0" width="922" height="400" fill="var(--ink-black)"/>
        <text class="brand-name" x="261" y="64" fill="var(--paper)">MAPLE DEW GALA</text>
        <use href="#badge-tan"/>
      </symbol>

      <!-- Tan label -->
      <symbol id="label-tan" viewBox="0 0 522 320" overflow="visible">
        <rect x="-200" y="0" width="922" height="400" fill="url(#tan-glow)"/>
        <text class="brand-name" x="261" y="64" fill="var(--paper)">MAPLE DEW GALA</text>
        <use href="#wreath-shape" fill="url(#wreath-tone)" role="img" aria-label="Wreath of green leaves and golden oil drops"/>
        <circle cx="261" cy="205" r="86" fill="var(--paper)"/>
        <text class="claim-pct" x="261" y="143" fill="var(--tan)">100%</text>
        <text class="claim-organic" x="261" y="158" fill="var(--tan)">PURE ORGANIC</text>
        <text class="product-name product-name--coconut" x="261" y="196" textLength="128" lengthAdjust="spacingAndGlyphs" fill="var(--tan)">COCONUT</text>
        <text class="product-name product-name--oil" x="257" y="240" textLength="56" lengthAdjust="spacingAndGlyphs" fill="var(--tan)">OIL</text>
        <circle cx="317" cy="225" r="17" fill="var(--tan-soft)"/>
        <text class="size-note" x="317" y="222" fill="var(--paper)">8 FL OZ</text>
        <text class="size-note" x="317" y="229" fill="var(--paper)">236mL</text>
      </symbol>

      <!-- Black label with glow -->
      <symbol id="label-noir" viewBox="0 0 522 320" overflow="visible">
        <rect x="-200" y="0" width="922" height="400" fill="url(#noir-glow)"/>
        <text class="brand-name" x="261" y="64" fill="var(--paper)">MAPLE DEW GALA</text>
        <use href="#badge-tan"/>
      </symbol>

      <path id="bottle-outline" d="M70,0 L136,0 L139,30 L137,42 L142,240 C150,330 206,360 206,420 C206,472 160,500 103,500 C46,500 0,472 0,420 C0,360 56,330 64,240 L69,42 L67,30 Z"/>
      <clipPath id="bottle-clip"><use href="#bottle-outline"/></clipPath>
    </defs>
  </svg>

  <!-- Flat label concepts -->
  <svg class="flat-label flat-label--white" viewBox="0 0 522 247" overflow="hidden" role="img" aria-label="White label concept">
    <use href="#label-white" x="0" y="0" width="522" height="320"/>
  </svg>
  <svg class="flat-label flat-label--black" viewBox="0 0 522 247" overflow="hidden" role="img" aria-label="Black label concept">
    <use href="#label-black" x="0" y="0" width="522" height="320"/>
  </svg>
  <svg class="flat-label flat-label--tan" viewBox="0 0 522 247" overflow="hidden" role="img" aria-label="Tan label concept">
    <use href="#label-tan" x="0" y="0" width="522" height="320"/>
  </svg>
  <svg class="flat-label flat-label--noir" viewBox="0 0 522 247" overflow="hidden" role="img" aria-label="Black glow label concept">
    <use href="#label-noir" x="0" y="0" width="522" height="320"/>
  </svg>

  <!-- Bottle mockups -->
  <svg class="bottle bottle--white" viewBox="0 0 206 500" role="img" aria-label="Bottle with white label">
    <use href="#bottle-outline" class="glass"/>
    <rect class="glass-seam" x="72" y="275" width="3" height="22"/>
    <g clip-path="url(#bottle-clip)">
      <svg x="-103" y="294" width="412" height="253" viewBox="0 0 522 320" overflow="hidden">
        <use href="#label-white" width="522" height="320"/>
      </svg>
      <rect x="0" y="294" width="206" height="210" fill="url(#white-fade)" opacity="0.35"/>
    </g>
  </svg>

  <svg class="bottle bottle--tan" viewBox="0 0 206 500" role="img" aria-label="Bottle with tan label">
    <use href="#bottle-outline" class="glass"/>
    <rect class="glass-seam" x="72" y="275" width="3" height="22"/>
    <g clip-path="url(#bottle-clip)">
      <svg x="-103" y="294" width="412" height="253" viewBox="0 0 522 320" overflow="hidden">
        <use href="#label-tan" width="522" height="320"/>
      </svg>
    </g>
  </svg>

  <svg class="bottle bottle--black" viewBox="0 0 206 500" role="img" aria-label="Bottle with black label">
    <use href="#bottle-outline" class="glass"/>
    <rect class="glass-seam" x="72" y="275" width="3" height="22"/>
    <g clip-path="url(#bottle-clip)">
      <svg x="-103" y="294" width="412" height="253" viewBox="0 0 522 320" overflow="hidden">
        <use href="#label-black" width="522" height="320"/>
      </svg>
    </g>
  </svg>

  <svg class="bottle bottle--noir" viewBox="0 0 206 500" role="img" aria-label="Bottle with black label and white name">
    <use href="#bottle-outline" class="glass"/>
    <rect class="glass-seam" x="131" y="275" width="3" height="22"/>
    <g clip-path="url(#bottle-clip)">
      <svg x="-103" y="294" width="412" height="253" viewBox="0 0 522 320" overflow="hidden">
        <use href="#label-black-white-name" width="522" height="320"/>
      </svg>
    </g>
  </svg>

</main>
</body>
</html>
```